Duct Manufacturing Company new to the industry needs business card and stationary design

we are sheet metal duct manufacturers looking for a business card design to fit my new business logo.
nothing to crazy that will date, but want it to stand out from the crowed.
I'm sure you guys will work it out.

Contact Information for Business Card

Glen Marsh
Director

Address
17 Dorwell St
Carrowby NSW 2719

0438 760 514

Sales@flowbend.com.au

Font styles to use
Other font styles liked:
• BankGothic md bt

Requirements
Nice to have
• Like the idea of corner rounded to match logo
• like to keep colours flowing
• font I like sharp square not rounded

```html
<!DOCTYPE html>
<html lang="en">
<head>
<meta charset="utf-8">
<title>Flowbend Industries – Business Card</title>
<link href="https://fonts.googleapis.com/css2?family=Saira:wght@400;600&display=swap" rel="stylesheet">
<style>
  :root {
    --backdrop: #3a3a3a;
    --blue-deep: #0b4a9c;
    --blue-mid: #1565c0;
    --blue-light: #2a86d8;
    --green: #7bc043;
    --green-dark: #4f9a2a;
    --white: #ffffff;
    --paper: #f6f6f6;
  }
  html, body {
    margin: 0;
    padding: 0;
    width: 1200px;
    height: 750px;
    overflow: hidden;
    background: var(--backdrop);
    font-family: "Saira", sans-serif;
  }
  .card {
    position: absolute;
    top: 228px;
    width: 461px;
    height: 262px;
    overflow: hidden;
    background: radial-gradient(ellipse at 40% 60%, var(--blue-light) 0%, var(--blue-mid) 45%, var(--blue-deep) 100%);
  }
  .card--front { left: 124px; }
  .card--back {
    left: 618px;
    background: radial-gradient(ellipse at 50% 45%, var(--blue-light) 0%, var(--blue-mid) 50%, var(--blue-deep) 100%);
  }
  .front-shapes { position: absolute; inset: 0; }

  .brand {
    position: absolute;
    left: 268px;
    top: 62px;
    width: 160px;
    text-align: center;
    color: var(--blue-mid);
    font-weight: 600;
    text-transform: uppercase;
    line-height: 1.05;
  }
  .brand__name { font-size: 24px; letter-spacing: 0.5px; display: block; }
  .brand__sub { font-size: 15px; letter-spacing: 3px; display: block; }

  .contact {
    position: absolute;
    left: 25px;
    top: 112px;
    color: var(--white);
  }
  .contact__name {
    margin: 0;
    font-size: 19px;
    font-weight: 600;
    color: var(--green);
    line-height: 22px;
  }
  .contact__role {
    margin: 0 0 8px;
    font-size: 13px;
    font-weight: 400;
    color: var(--green);
    line-height: 16px;
  }
  .contact__address {
    font-style: normal;
    font-size: 11px;
    line-height: 14.5px;
    margin-bottom: 6px;
  }
  .contact__line {
    display: flex;
    align-items: center;
    gap: 7px;
    font-size: 11px;
    line-height: 17.5px;
  }
  .contact__line svg { width: 12px; height: 12px; flex: none; }

  .back-brand {
    position: absolute;
    left: 0;
    right: 0;
    top: 110px;
    text-align: center;
    color: var(--white);
    font-weight: 600;
    font-size: 34px;
    letter-spacing: 2px;
    text-transform: uppercase;
  }
  .back-url {
    position: absolute;
    left: 0;
    right: 0;
    top: 222px;
    text-align: center;
    color: var(--white);
    font-size: 11px;
    letter-spacing: 5px;
  }
</style>
</head>
<body>
  <section class="card card--front">
    <svg class="front-shapes" viewBox="0 0 461 262" width="461" height="262" aria-hidden="true">
      <path d="M190 0 C220 110 300 200 357 262 L461 262 L461 0 Z" fill="var(--paper)"/>
      <path d="M163 0 L190 0 C220 110 300 200 357 262 L353 262 C290 205 200 120 163 0 Z" fill="var(--green)"/>
      <path d="M163 0 C200 120 290 205 353 262" fill="none" stroke="var(--white)" stroke-width="1.5"/>
    </svg>

    <div class="brand">
      <span class="brand__name">Flowbend</span>
      <span class="brand__sub">Industries</span>
    </div>

    <div class="contact">
      <h1 class="contact__name">Glen Marsh</h1>
      <p class="contact__role">Director</p>
      <address class="contact__address">17 Dorwell St<br>Carrowby NSW 2719</address>
      <div class="contact__line">
        <svg viewBox="0 0 12 12" aria-hidden="true"><path d="M2.5 1 L4.5 1 L5 3.5 L3.8 4.5 C4.5 6 6 7.5 7.5 8.2 L8.5 7 L11 7.5 L11 9.5 C11 10.3 10.3 11 9.5 11 C5 11 1 7 1 2.5 C1 1.7 1.7 1 2.5 1 Z" fill="var(--green)"/></svg>
        <span>0438 760 514</span>
      </div>
      <div class="contact__line">
        <svg viewBox="0 0 12 12" aria-hidden="true"><rect x="0.5" y="2.5" width="11" height="7.5" fill="var(--green)"/><path d="M0.5 2.5 L6 7 L11.5 2.5" fill="none" stroke="var(--blue-mid)" stroke-width="1"/></svg>
        <span>Sales@flowbend.com.au</span>
      </div>
      <div class="contact__line">
        <svg viewBox="0 0 12 12" aria-hidden="true"><circle cx="6" cy="6" r="5.5" fill="var(--green)"/><path d="M3 3.5 C4.5 4 4 6 5.5 6.5 C6.5 7 6 9 7 10 M8 2 C7.5 3.5 9 4.5 10.5 4.5" fill="none" stroke="var(--blue-mid)" stroke-width="1"/></svg>
        <span>www.flowbend.com.au</span>
      </div>
    </div>
  </section>

  <section class="card card--back">
    <div class="back-brand">Flowbend</div>
    <div class="back-url">www.flowbend.com</div>
  </section>
</body>
</html>
```